Small environmental consultancy needs a simple but professional web design

We are a boutique environmental consultancyand contracting business located in Margaret River in the South West of Western Australia.

We have two arms
1) Consulting which offers environmental planning, management and assessment services primarily to local government and the development industry.
2) Contracting which implements on site plans and on ground works primarily involving revegetation, bush regeneration and environmental weed control.

We need a simple yet professional web design within the wordpress platform that commmunicates professionalism, experience and technical expertise without appearing too corporate.

Something like this structure appeals:
http://fernquill.net.au/environment-services/
or
http://www.tallowbrookenvironmental.com.au/index.php

(without the image gallery function)

Target Market(s)

Local Government Officers deciding on tenders;
Developers, Engineers, Town Planning consultants looking for environmental expertise

Industry/Entity Type

Business

Number of Pages Required

5+ page

Font styles to use
Sans Serif

Colors
33a6d7
9bcb3c

Requirements
Must have
• Pages required include:
• Home
• Environmental Planning and Management
• Revegetation and Regeneration Implementation (This page can mirror the Environmental Planning and Management page exactly in structure but with different text and images)
• About Us (I think that this page can be relatively simple and generic)
• Contact (I think that this page can be very simple and generic)
Nice to have
• An ability to start out basic and quicikly establish a website presence and then build in additional drop downs and pages over time.
Should not have
• It does not need a photo gallery page;
• It does not need a major amount of space dedicated to social media and blogs etc as this is not currently particularly active area for us

```html
<!DOCTYPE html>
<html lang="en">
<head>
<meta charset="utf-8">
<title>Banksia Ridge Ecoservices – Environmental Planning and Management</title>
<link rel="stylesheet" href="https://fonts.googleapis.com/css2?family=Open+Sans:wght@400;600;700&family=Raleway:wght@700&family=Teko:wght@400;500&display=swap">
<style>
  :root {
    --blue: #33a6d7;
    --blue-dark: #1f84bf;
    --blue-line: #2389bd;
    --green: #9bcb3c;
    --green-dark: #7a9a1a;
    --brown: #7a4b1e;
    --text: #555555;
    --heading-dark: #3a3a3a;
    --header-bg: #ededed;
    --footer-bg: #ececec;
    --rule: #d8d8d8;
    --field-border: #d9d9d9;
    --icon: #a9a9a9;
    --white: #ffffff;
  }
  * { box-sizing: border-box; margin: 0; padding: 0; }
  html, body { width: 1064px; height: 1200px; overflow: hidden; }
  body {
    position: relative;
    background: var(--white);
    font-family: "Open Sans", Arial, sans-serif;
    color: var(--text);
  }

  /* Header */
  .site-header {
    position: absolute; left: 0; top: 0; width: 1064px; height: 155px;
    background: linear-gradient(180deg, #efefef 0%, #e8e8e8 100%);
  }
  .brand {
    position: absolute; left: 64px; top: 44px;
    display: flex; align-items: center; gap: 16px;
  }
  .brand-mark {
    width: 58px; height: 58px; border-radius: 50%; background: var(--green);
  }
  .brand-name {
    font-family: "Open Sans", Arial, sans-serif; font-weight: 600;
    font-size: 32px; color: var(--brown); letter-spacing: 0.2px;
  }
  .header-call {
    position: absolute; right: 64px; top: 32px; text-align: left;
  }
  .header-call .label {
    font-weight: 700; font-size: 15px; color: #222; line-height: 20px;
  }
  .header-call .number {
    font-weight: 700; font-size: 25px; color: var(--blue); line-height: 28px; letter-spacing: 0.3px;
  }
  .search {
    position: absolute; left: 809px; top: 93px; width: 189px; height: 24px;
    background: var(--white); border-radius: 2px;
    font-size: 12px; color: #555; padding: 4px 10px;
  }
  .search svg { position: absolute; right: 7px; top: 5px; }

  /* Navigation */
  .main-nav {
    position: absolute; left: 0; top: 155px; width: 1064px; height: 40px;
    background: var(--blue); border-bottom: 3px solid var(--blue-line);
  }
  .main-nav a {
    position: absolute; top: 0; height: 37px; line-height: 37px;
    font-family: "Raleway", Arial, sans-serif; font-weight: 700; font-size: 12.5px;
    color: var(--white); text-decoration: none; text-transform: uppercase;
  }
  .main-nav a.is-active {
    background: var(--blue-dark); padding: 0 20px;
  }

  /* Hero band */
  .hero {
    position: absolute; left: 0; top: 195px; width: 1064px; height: 111px;
    background: linear-gradient(90deg, #4f6a2c 0%, #8aa35a 20%, #3f5a24 40%, #7f9a4c 60%, #4b6328 80%, #8a9a3e 100%);
  }

  /* Content */
  .content { position: absolute; left: 65px; top: 338px; width: 934px; }
  .page-title {
    font-family: "Teko", "Arial Narrow", sans-serif; font-weight: 500;
    font-size: 40px; line-height: 46px; color: var(--green);
    text-transform: uppercase; letter-spacing: 0.3px;
  }
  .content p {
    font-size: 12.4px; line-height: 18.7px; color: var(--text);
    margin-bottom: 18px;
  }
  .intro { display: flex; justify-content: space-between; margin-top: 12px; }
  .intro-text { width: 532px; }
  .feature-photo {
    width: 373px; height: 253px; margin-top: 2px;
    background: radial-gradient(ellipse at 45% 45%, #e6dcd0 0%, #a9a473 22%, #6f8a3e 55%, #4d6a2a 100%);
  }

  /* Footer */
  .site-footer {
    position: absolute; left: 0; top: 910px; width: 1064px; height: 290px;
    background: var(--footer-bg); border-top: 1px solid var(--rule);
  }
  .footer-heading {
    position: absolute;
    font-family: "Teko", "Arial Narrow", sans-serif; font-weight: 400;
    font-size: 21px; line-height: 24px; color: var(--heading-dark); text-transform: uppercase;
  }
  .footer-links {
    position: absolute; list-style: none; font-size: 12.4px; line-height: 18.3px; color: #444;
  }
  .footer-call {
    position: absolute; left: 65px; top: 136px;
  }
  .footer-call .label {
    font-family: "Teko", "Arial Narrow", sans-serif; font-size: 21px; line-height: 24px;
    color: var(--heading-dark); text-transform: uppercase;
  }
  .footer-call .number {
    display: flex; align-items: center; gap: 6px; margin-top: 4px;
    font-family: "Teko", "Arial Narrow", sans-serif; font-weight: 500;
    font-size: 32px; line-height: 34px; color: var(--green); letter-spacing: 0.5px;
  }
  .contact-form { position: absolute; left: 545px; top: 66px; width: 452px; }
  .field {
    position: absolute; background: var(--white); border: 1px solid var(--field-border);
    font-size: 13px; color: #aaa; padding: 7px 12px;
  }
  .field svg { position: absolute; right: 8px; top: 7px; }
  .field-name { left: 0; top: 0; width: 221px; height: 33px; }
  .field-email { left: 231px; top: 0; width: 221px; height: 33px; }
  .field-message { left: 0; top: 41px; width: 452px; height: 65px; }
  .send-button {
    position: absolute; left: 0; top: 115px; width: 138px; height: 38px;
    background: linear-gradient(180deg, #a3c03a 0%, var(--green-dark) 100%);
    border: 1px solid #6f8c17;
    font-family: "Teko", "Arial Narrow", sans-serif; font-size: 21px; line-height: 38px;
    color: var(--white); text-align: center; text-transform: uppercase;
  }
  .footer-rule {
    position: absolute; left: 65px; top: 246px; width: 957px; height: 1px; background: var(--rule);
  }
  .copyright {
    position: absolute; left: 65px; top: 259px; font-size: 12.4px; color: #444;
  }
</style>
</head>
<body>

<header class="site-header">
  <div class="brand">
    <span class="brand-mark"></span>
    <span class="brand-name">Banksia Ridge Ecoservices</span>
  </div>
  <div class="header-call">
    <div class="label">Call Us</div>
    <div class="number">0400 372 816</div>
  </div>
  <div class="search">Search
    <svg width="14" height="14" viewBox="0 0 14 14" aria-hidden="true">
      <circle cx="6" cy="6" r="4.5" fill="none" stroke="#999" stroke-width="1.8"/>
      <line x1="9.3" y1="9.3" x2="13" y2="13" stroke="#999" stroke-width="2"/>
    </svg>
  </div>
</header>

<nav class="main-nav">
  <a href="#" style="left:89px">Home</a>
  <a href="#" class="is-active" style="left:141px">Environmental Planning and Management</a>
  <a href="#" style="left:473px">Revegetation and Bush Regeneration</a>
  <a href="#" style="left:751px">About Us</a>
  <a href="#" style="left:848px">Contact</a>
</nav>

<div class="hero" role="img" aria-label="Banner photo of dense native bushland with trees and undergrowth"></div>

<main class="content">
  <h1 class="page-title">Environmental Planning and Management</h1>
  <div class="intro">
    <div class="intro-text">
      <p>Lorem ipsum dolor sit amet, consectetuer adipiscing elit, sed diam nonummy nibh euismod tincidunt ut laoreet dolore magna aliquam erat ullamcorper suscipit lobortis nisl ut aliquip ex ea commodo consequat. Lorem ipsum dolor sit amet, consectetuer adipiscing elit, sed diam nonummy nibh euismod tincidunt ut laoreet dolore magna aliquam erat volutpat. Ut wisi enim ad minim veniam, quis nostrud exerci tation ullamcorper suscipit lobortis nisl ut aliquip ex ea commodo consequat.Lorem ipsum dolor sit amet, consectetuer adipiscing elit, sed diam nonummy nibh euismod tincidunt ut laoreet dolore magna aliquam erat volutpat. Ut wisi enim ad minim veniam, quis nostrud exerci tation ullamcorper suscipit lobortis nisl ut aliquip ex ea commodo consequat.</p>
      <p>Lorem ipsum dolor sit amet, consectetuer adipiscing elit, sed diam nonummy nibh euismod tincidunt ut laoreet dolore magna aliquam erat volutpat. Ut wisi enim ad minim veniam, quis nostrud exerci tation ullamcorper suscipit lobortis nisl ut aliquip ex ea commodo consequat. Lorem ipsum dolor sit amet, consectetuer adipiscing elit, sed diam nonummy nibh euismod tincidunt ut laoreet dolore magna aliquam erat ullamcorper suscipit lobortis nisl ut aliquip ex ea commodo consequat.</p>
    </div>
    <div class="feature-photo" role="img" aria-label="Photo of a white native spider orchid among grasses"></div>
  </div>
  <p>Lorem ipsum dolor sit amet, consectetuer adipiscing elit, sed diam nonummy nibh euismod tincidunt ut laoreet dolore magna aliquam erat ullamcorper suscipit lobortis nisl ut aliquip ex ea commodo consequat. Lorem ipsum dolor sit amet, consectetuer adipiscing elit, sed diam nonummy nibh euismod tincidunt ut laoreet dolore magna aliquam erat volutpat. Ut wisi enim ad minim veniam, quis nostrud exerci tation ullamcorper suscipit lobortis nisl ut aliquip ex ea commodo consequat.Lorem ipsum dolor sit amet, consectetuer adipiscing elit, sed diam nonummy nibh euismod tincidunt ut laoreet dolore magna aliquam erat volutpat. Ut wisi enim ad minim veniam, quis nostrud exerci tation ullamcorper suscipit lobortis nisl ut aliquip ex ea commodo consequat.</p>
  <p>Lorem ipsum dolor sit amet, consectetuer adipiscing elit, sed diam nonummy nibh euismod tincidunt ut laoreet dolore magna aliquam erat volutpat. Ut wisi enim ad minim veniam, quis nostrud exerci tation ullamcorper suscipit lobortis nisl ut aliquip ex ea commodo consequat. Lorem ipsum dolor sit amet, consectetuer adipiscing elit, sed diam nonummy nibh euismod tincidunt ut laoreet dolore magna aliquam erat ullamcorper suscipit lobortis nisl ut aliquip ex ea commodo consequat.</p>
</main>

<footer class="site-footer">
  <h2 class="footer-heading" style="left:65px; top:36px">About</h2>
  <ul class="footer-links" style="left:65px; top:65px">
    <li>Environmental Planning and Management</li>
    <li>Revegetation and Bush Regeneration</li>
    <li>Contacts</li>
  </ul>

  <h2 class="footer-heading" style="left:334px; top:36px">Website</h2>
  <ul class="footer-links" style="left:334px; top:64px">
    <li>www.banksiaridgeeco.com.au</li>
  </ul>

  <div class="footer-call">
    <div class="label">Call us now:</div>
    <div class="number">
      <svg width="20" height="20" viewBox="0 0 20 20" aria-hidden="true">
        <path d="M4 2 L7.5 2 L9 6.5 L6.8 8.2 C7.8 10.4 9.6 12.2 11.8 13.2 L13.5 11 L18 12.5 L18 16 C18 17.2 17 18 15.8 18 C8.3 17.4 2.6 11.7 2 4.2 C2 3 2.8 2 4 2 Z" fill="#555"/>
      </svg>
      0400 372 816
    </div>
  </div>

  <h2 class="footer-heading" style="left:545px; top:36px">Contact Us</h2>
  <form class="contact-form">
    <div class="field field-name">Name
      <svg width="18" height="18" viewBox="0 0 18 18" aria-hidden="true">
        <circle cx="9" cy="5" r="4" fill="var(--icon)"/>
        <path d="M1 18 C1 12 4.5 10 9 10 C13.5 10 17 12 17 18 Z" fill="var(--icon)"/>
      </svg>
    </div>
    <div class="field field-email">E-mail
      <svg width="20" height="16" viewBox="0 0 20 16" aria-hidden="true" style="top:8px">
        <rect x="0" y="1" width="20" height="14" rx="1.5" fill="var(--icon)"/>
        <path d="M1 2 L10 9 L19 2" fill="none" stroke="#fff" stroke-width="1.6"/>
      </svg>
    </div>
    <div class="field field-message">Message
      <svg width="20" height="18" viewBox="0 0 20 18" aria-hidden="true" style="top:4px">
        <path d="M1 1 H19 V12 H8 L4 16 V12 H1 Z" fill="var(--icon)"/>
        <circle cx="6" cy="6.5" r="1.2" fill="#fff"/><circle cx="10" cy="6.5" r="1.2" fill="#fff"/><circle cx="14" cy="6.5" r="1.2" fill="#fff"/>
      </svg>
    </div>
    <div class="send-button">Send Message</div>
  </form>

  <div class="footer-rule"></div>
  <p class="copyright">© 2015 Banksia Ridge Ecoservices. All Rights Reserved.</p>
</footer>

</body>
</html>
```